Venture Capital firm needs modern business cards

We are a Venture Capital firm within financial services/Asset management. The industry generally has basic business cards with black, blue and maybe green/yellow design elements.
Our firm has a four-colour swoosh logo. We are based in London and want to stand out, just a little bit!, from the crowd. Our company is called LORV Investments and the 'C' stands for collaboration thus using makerswarm is a natural portal for our business card design competition. Our logo came via makerswarm too!
We use 'Venture Partner in Asset Management' as our tagline and this is Trademark registered. We operate in a conservative industry and we should not overstep our mark. The logo is colorful as it is and therefore the rest of the design should not be too fanciful.
The objective is twofold: make our logo element stick and memorable with our audience, whilst representing a conservative yet young image.
Updates
The Business Card obviously needs a field for Name, Surname, Job Title, Adress fields: Street, City, Postcode, Country, telefone and cell number, website address, etc.
We have uploaded the ai file. We trust that these are OK. If not, please advise.
Reason: We have have been busy with a client engagement. We will set the project as Guaranteed in return for the troubles we cause. Apologies for the confusion.
Thank you all for these great and creative design suggestions. The team is very happy with a number of your ideas! We will be in touch tomorrow to give individual feedback before the project closes on Friday. We look forward to working with some of you to narrow down your creations. Thank you, LORV Investments team.
All,
Target Market(s)
Financial Services Professionals, Investors, Media, 35-70 years, mainly male, well educated
Industry/Entity Type
Conservative
Requirements
Must have
- We must make use of our logo and potential tagline 'Venture Partner in Asset Management' as we are establishing a new Brand and new company in the market.
We can use 'LORV', 'LORV Investments', and 'LORV Investments'+tagline 'Venture Partner in Asset Management' or simply the four-colour swoosh plus the name of the company as part of the text. (see files)
All design elements are available in black or grey-scale if required. (grey scale swoosh attached).
Due to regulation we must have the following wording on the card in small print 'LORV Investments is an Appointed Representative of Bramwell Holdings Partnership Limited, which is authorised by the Monetary Oversight Board'.
Nice to have
- We would consider designs that make use of different printing techniques such embossing/debossing, UV spot etc.
We attach our colour palette in the files section for your reference.
Should not have
- The font we use for our company name is 'EXO' so do not use a font style that clashes with the corporate fonts, please.
Do not use other design elements than the ones we provide in the file library as part of this project.

```html
<!DOCTYPE html>
<html lang="en">
<head>
<meta charset="utf-8">
<title>LORV Investments – Business Card</title>
<link rel="stylesheet" href="https://fonts.googleapis.com/css2?family=Exo:wght@200;300;400;500&family=Titillium+Web:wght@400;600&display=swap">
<style>
  :root {
    --backdrop: #b4b4b4;
    --card-light: #ffffff;
    --card-dark: #242424;
    --ink: #3c3d3d;
    --ink-soft: #6f7072;
    --accent-green: #7dbb3c;
    --accent-orange: #f7a21b;
    --accent-teal: #1aa6bf;
    --accent-pink: #e3306e;
    --tagline: #e6e6e6;
  }
  * { box-sizing: border-box; margin: 0; padding: 0; }
  html, body { width: 1200px; height: 487px; overflow: hidden; }
  body {
    background: var(--backdrop);
    position: relative;
    font-family: "Titillium Web", Arial, sans-serif;
  }
  .card {
    position: absolute;
    top: 80px;
    width: 532px;
    height: 325px;
    border-radius: 18px;
    overflow: hidden;
  }
  .card--front { left: 53px; background: var(--card-light); }
  .card--back { left: 607px; background: var(--card-dark); }

  /* front */
  .brand {
    position: absolute;
    left: 100px;
    top: 78px;
    display: flex;
    align-items: center;
    gap: 14px;
  }
  .brand__dot {
    width: 22px; height: 22px;
    border-radius: 50%;
    background: var(--accent-green);
  }
  .brand__name {
    font-family: "Exo", Arial, sans-serif;
    font-weight: 400;
    font-size: 46px;
    color: var(--ink);
    letter-spacing: 0.5px;
  }
  .holder {
    position: absolute;
    left: 28px;
    top: 234px;
  }
  .holder__name {
    font-weight: 600;
    font-size: 16.5px;
    color: var(--ink-soft);
    letter-spacing: 0.3px;
  }
  .holder__role {
    font-size: 13.5px;
    color: var(--accent-green);
    text-align: right;
    margin-top: 2px;
  }
  .contact {
    position: absolute;
    left: 254px;
    top: 234px;
    list-style: none;
    font-size: 13px;
    line-height: 15.5px;
    color: var(--ink-soft);
  }
  .contact li { display: flex; align-items: flex-start; gap: 7px; }
  .contact svg { width: 11px; height: 11px; margin-top: 2px; flex: none; fill: var(--accent-green); }
  .contact .phones { gap: 7px; }
  .contact .phones span + svg { margin-left: 8px; }

  /* back */
  .glow { position: absolute; inset: 0; }
  .tagline {
    position: absolute;
    left: 160px;
    top: 80px;
    font-family: "Exo", Arial, sans-serif;
    font-weight: 300;
    color: var(--tagline);
    line-height: 1;
  }
  .tagline__small { font-size: 28px; display: block; }
  .tagline__large { font-size: 44px; display: block; margin-top: 2px; }
  .tagline__in { font-size: 16px; vertical-align: 22px; margin-right: 2px; }
  .tagline__mgmt { font-size: 30px; display: block; margin-top: 2px; }
  .tagline__url {
    display: block;
    font-family: "Titillium Web", Arial, sans-serif;
    font-weight: 400;
    font-size: 14.5px;
    color: #ffffff;
    margin-top: 6px;
  }
  .tagline__url b { color: var(--accent-green); font-weight: 400; }
</style>
</head>
<body>

<section class="card card--front">
  <div class="brand">
    <span class="brand__dot"></span>
    <span class="brand__name">LORV Investments</span>
  </div>

  <div class="holder">
    <p class="holder__name">CARDHOLDER NAME</p>
    <p class="holder__role">Designation</p>
  </div>

  <ul class="contact">
    <li>
      <svg viewBox="0 0 12 12"><path d="M6 0a4 4 0 0 0-4 4c0 3 4 8 4 8s4-5 4-8a4 4 0 0 0-4-4zm0 5.6A1.6 1.6 0 1 1 6 2.4a1.6 1.6 0 0 1 0 3.2z"/></svg>
      <span>01 01 Avenue, Suite No. 123,<br>Your City, Country</span>
    </li>
    <li class="phones">
      <svg viewBox="0 0 12 12"><circle cx="6" cy="6" r="6"/><path d="M4 3l1 1.6-.6.8a4 4 0 0 0 2.2 2.2l.8-.6L9 8l-.6 1c-3 0-5.4-2.4-5.4-5.4z" fill="#fff"/></svg>
      <span>+012 345 6789</span>
      <svg viewBox="0 0 12 12"><path d="M3 0h6v4H3zM1 5h10v5H1zM3 8h6v4H3z"/></svg>
      <span>+012 345 6780</span>
    </li>
    <li>
      <svg viewBox="0 0 12 12"><path d="M0 2h12v8H0z"/><path d="M0 2l6 4 6-4" fill="none" stroke="#fff" stroke-width="1"/></svg>
      <span>cardholder.name@lorvinvestments.com</span>
    </li>
    <li>
      <svg viewBox="0 0 12 12"><circle cx="6" cy="6" r="6"/><path d="M0 6h12M6 0c-3 3-3 9 0 12M6 0c3 3 3 9 0 12" fill="none" stroke="#fff" stroke-width=".8"/></svg>
      <span>www.lorvinvestments.com</span>
    </li>
  </ul>
</section>

<section class="card card--back">
  <svg class="glow" viewBox="0 0 532 325" preserveAspectRatio="none" aria-hidden="true">
    <defs>
      <radialGradient id="glow-green" cx="0" cy="0.8" r="0.45"><stop offset="0" stop-color="#7dbb3c" stop-opacity=".55"/><stop offset="1" stop-color="#7dbb3c" stop-opacity="0"/></radialGradient>
      <radialGradient id="glow-orange" cx="0.25" cy="0" r="0.35"><stop offset="0" stop-color="#f7a21b" stop-opacity=".5"/><stop offset="1" stop-color="#f7a21b" stop-opacity="0"/></radialGradient>
      <radialGradient id="glow-teal" cx="1" cy="0.2" r="0.45"><stop offset="0" stop-color="#1aa6bf" stop-opacity=".55"/><stop offset="1" stop-color="#1aa6bf" stop-opacity="0"/></radialGradient>
      <radialGradient id="glow-pink" cx="0.8" cy="1" r="0.35"><stop offset="0" stop-color="#e3306e" stop-opacity=".5"/><stop offset="1" stop-color="#e3306e" stop-opacity="0"/></radialGradient>
    </defs>
    <rect width="532" height="325" fill="url(#glow-green)"/>
    <rect width="532" height="325" fill="url(#glow-orange)"/>
    <rect width="532" height="325" fill="url(#glow-teal)"/>
    <rect width="532" height="325" fill="url(#glow-pink)"/>
  </svg>

  <h2 class="tagline">
    <span class="tagline__small">Venture</span>
    <span class="tagline__large">Partner</span>
    <span class="tagline__large"><span class="tagline__in">in</span>Asset</span>
    <span class="tagline__mgmt">Management</span>
    <span class="tagline__url">www.<b>lorvinvestments</b>.com</span>
  </h2>
</section>

</body>
</html>
```